Brightvale cleaning and maintenance company

An expansive website whereby we can advertise our commercial cleaning and maintenance services across a service portfolio of commercial cleaning and property maintenance. Whereby potential skilled resources can deposit there resume so we can collaborate and match candidates to a broad range of cleaning and maintenance jobs/projects.
Updates

Looking for more extensive ideas so the front page can change pictures on it with the focus for Brightvale Commercial Cleaning and Maintenance. Also need to bring in all the portfolios we offer including 1. Equipment Cleaning and Sanitisation Services 2. High pressure gurney and play ground equipment cleaning 3. General Cleaning and Property Facilities Management 4. Project and Recruiting Services, to allow for potential professional cleaners, handy man, mechanics, warehousing resources , electricians to deposit there resume. Most of the designers have stuck with the old portfolio categories , however the portfolio of services we offer has been updated so that needs to be reflected in the website. Also not necessary to use all my original photos I would like the opening page of the website to perhaps be able to change and have different pictures is that possible thank you

```html
<!DOCTYPE html>
<html lang="en">
<head>
<meta charset="utf-8">
<title>Brightvale — Commercial Cleaning &amp; Maintenance</title>
<link href="https://fonts.googleapis.com/css2?family=Lato:wght@400;700;900&display=swap" rel="stylesheet">
<style>
:root{
  --navy:#1b2f63;
  --navy-dark:#14254f;
  --red:#f2400f;
  --card:#f0f0f0;
  --text:#4a4a4a;
  --white:#ffffff;
}
*{box-sizing:border-box;margin:0;padding:0}
html,body{width:1200px;height:5034px;overflow:hidden}
body{font-family:'Lato',sans-serif;color:var(--text);background:var(--white);position:relative}
.abs{position:absolute}
.center{left:0;width:1200px;text-align:center}
svg.band{position:absolute;left:0;display:block}

/* header */
.topline{top:0;left:0;width:1200px;height:6px;background:var(--navy)}
.phonebar{top:0;left:780px;width:420px;height:51px}
.phonebar-text{top:13px;left:812px;color:var(--white);font-size:18px;font-weight:700;display:flex;align-items:center;gap:10px}
.phonebar-text strong{font-size:22px;font-weight:700}
.logo{top:40px;left:74px;display:flex;align-items:center;gap:14px}
.logo-mark{width:54px;height:54px;border-radius:50%;background:var(--navy)}
.logo-name{font-size:40px;font-weight:700;color:var(--red);letter-spacing:-.5px}
.nav{top:94px;right:72px;display:flex;gap:30px;font-size:13px;font-weight:700;color:#2a2a2a}
.nav a{color:inherit;text-decoration:none;position:relative}
.nav a.active{color:var(--red)}
.nav a.active::before{content:"";position:absolute;left:50%;top:-20px;width:14px;height:14px;margin-left:-7px;border-radius:50%;background:var(--navy)}
.nav a.active::after{content:"";position:absolute;left:-4px;right:-4px;top:21px;height:3px;background:var(--red)}

/* hero */
.hero{top:121px;left:0;width:1200px;height:690px;background:linear-gradient(135deg,#3a3f47 0%,#6f7479 40%,#9c9fa2 60%,#4d5258 100%)}
.hero-title{top:300px;font-size:92px;font-weight:700;color:var(--white);letter-spacing:1px}
.hero-sub{top:418px;font-size:22px;font-weight:700;color:var(--white);line-height:35px}
.btn{display:inline-block;background:var(--red);color:var(--white);font-weight:700;font-size:16px;border-radius:26px;text-align:center;line-height:48px;height:48px}
.hero-btn{top:515px;left:505px;width:190px}
.dots{top:652px;left:566px;display:flex;gap:10px}
.dots span{width:11px;height:11px;border-radius:50%;background:var(--white)}
.dots span:first-child{background:#2f7fd0}

/* section heads */
.mark{width:34px;height:34px;border-radius:50%;background:var(--navy)}
.mark.light{background:var(--white)}
.sec-title{font-size:28px;font-weight:900;color:var(--navy);text-transform:uppercase;letter-spacing:.3px}
.sec-title.light{color:var(--white)}
.rule{width:108px;height:2px;background:var(--red)}
.rule.light{background:var(--white)}

/* welcome */
.lead{font-size:20px;font-weight:700;color:var(--red)}
.body-text{font-size:15px;line-height:31px;color:var(--text)}

/* services */
.card{top:1505px;width:242px;height:395px;background:var(--card);border-radius:8px;overflow:hidden;text-align:center}
.card-img{height:176px;width:100%}
.card h3{margin-top:21px;font-size:17px;font-weight:700;color:var(--navy);line-height:21px;text-transform:uppercase}
.card p{margin:13px auto 0;width:214px;font-size:13px;line-height:25px;color:#333}
.card .go{position:absolute;left:111px;bottom:26px;width:20px;height:20px;border-radius:50%;background:var(--red)}
.card .go svg{display:block}

/* support */
.support{top:1970px;left:0;width:1200px;height:688px;background:var(--navy)}
.photo-circle{border-radius:50%;border:8px solid #3f5a92}
.support-title{top:2068px;left:586px;font-size:29px;font-weight:900;color:var(--white)}
.list{top:2156px;left:588px;color:var(--white);font-size:15px;list-style:none}
.list li{display:flex;gap:19px;line-height:31px;margin-bottom:12px}
.list li svg{flex:none;margin-top:8px}

/* gallery */
.shot{width:331px;height:209px}

/* people */
.people{top:3357px;left:0;width:1200px;height:698px;background:var(--navy)}

/* clients */
.client{top:4338px;width:164px;height:90px;border:1px solid #cfcfcf;display:flex;align-items:center;justify-content:center;gap:8px;font-size:18px;font-weight:700;color:var(--navy)}
.client i{width:14px;height:14px;border-radius:50%;background:var(--red);display:block}

/* footer */
.footer{top:4485px;left:0;width:1200px;height:478px;background:linear-gradient(160deg,var(--navy) 0%,var(--navy) 35%,#7b3748 60%,var(--red) 100%)}
.foot-col{top:4716px;color:var(--white);font-size:14px}
.foot-col h4{font-size:15px;font-weight:900;margin-bottom:10px;letter-spacing:.3px}
.foot-col li{list-style:none;line-height:31px}
.contact-row{display:flex;gap:20px;align-items:center}
.email-input{width:243px;height:43px;background:var(--white);border:1px solid #ccc;font-size:13px;color:#555;padding:0 12px;line-height:41px}
.signup{margin:12px 0 0 153px;width:90px;height:41px;background:var(--navy);color:var(--white);font-size:14px;font-weight:700;text-align:center;line-height:41px;border-radius:3px}
.bottombar{top:4963px;left:0;width:1200px;height:71px;background:var(--navy-dark)}
.copy{top:4990px;left:74px;color:#d7dbe6;font-size:11px}
.social{top:4986px;left:940px;display:flex;gap:22px}
.social span{width:18px;height:18px;border-radius:50%;background:var(--white);display:block}
</style>
</head>
<body>

<!-- header -->
<div class="abs topline"></div>
<svg class="abs phonebar" viewBox="0 0 420 51" aria-hidden="true"><path d="M20 0H420V51H0Z" fill="#1b2f63"/></svg>
<div class="abs phonebar-text">
  <svg width="18" height="18" viewBox="0 0 24 24" aria-hidden="true"><path fill="#fff" d="M6.6 10.8a15.1 15.1 0 0 0 6.6 6.6l2.2-2.2a1 1 0 0 1 1-.25 11.4 11.4 0 0 0 3.6.57 1 1 0 0 1 1 1V20a1 1 0 0 1-1 1A17 17 0 0 1 3 4a1 1 0 0 1 1-1h3.5a1 1 0 0 1 1 1c0 1.25.2 2.45.57 3.57a1 1 0 0 1-.25 1z"/></svg>
  <span>Head Office: <strong>(07) 5550 0123</strong></span>
</div>
<div class="abs logo"><span class="logo-mark"></span><span class="logo-name">Brightvale</span></div>
<nav class="abs nav">
  <a class="active">HOME</a><a>ABOUT US</a><a>SERVICES</a><a>OUR PEOPLE</a><a>SAFETY &amp; COMPLIANCE</a><a>CONTACT</a>
</nav>

<!-- hero -->
<div class="abs hero" role="img" aria-label="Rotating hero photo: cleaner at work in a stainless commercial kitchen"></div>
<h1 class="abs center hero-title">Brightvale</h1>
<p class="abs center hero-sub">Servicing Metropolitan Sydney, Brisbane, Melbourne, Adelaide, Newcastle<br>and Regional areas as required.</p>
<a class="abs btn hero-btn">GET A QUOTE</a>
<div class="abs dots"><span></span><span></span><span></span><span></span></div>
<svg class="band" style="top:620px" width="1200" height="192" viewBox="0 620 1200 192" aria-hidden="true"><path d="M0 811Q600 635 1200 811V812H0Z" fill="#fff"/></svg>

<!-- welcome -->
<div class="abs mark" style="top:829px;left:583px"></div>
<h2 class="abs center sec-title" style="top:884px">Welcome to Brightvale</h2>
<div class="abs rule" style="top:937px;left:546px"></div>
<p class="abs center lead" style="top:966px">We are Brightvale, a leading, Australian owned, cleaning services company.</p>
<p class="abs body-text" style="top:996px;left:74px;width:1052px;text-align:center">When you work with Brightvale it is easy to do business with us.<br>Our people are professional, reliable and service oriented. In every interaction you have; on site, receiving help from our service support staff, or rolling-out new cleaning sites, you will see and feel the benefits of using Brightvale. The pride we take in our work and a prevailing focus on employees, customers and partners, delivers a consistent and superior ongoing service.</p>
<a class="abs btn" style="top:1160px;left:510px;width:180px">READ MORE</a>

<!-- services -->
<svg class="band" style="top:1212px" width="1200" height="420" viewBox="0 1212 1200 420" aria-hidden="true">
  <defs><linearGradient id="svcGrad" x1="0" y1="0" x2="1" y2="0.35"><stop offset="0.15" stop-color="#f2400f"/><stop offset="0.5" stop-color="#4a2f58"/><stop offset="0.68" stop-color="#1b2f63"/></linearGradient></defs>
  <path d="M0 1212Q600 1406 1200 1212V1632H0Z" fill="url(#svcGrad)"/>
</svg>
<div class="abs mark light" style="top:1359px;left:583px"></div>
<h2 class="abs center sec-title light" style="top:1406px">Our Services</h2>

<div class="abs card" style="left:74px">
  <div class="card-img" role="img" aria-label="Photo: food service equipment being cleaned and sanitised" style="background:linear-gradient(160deg,#c9c3bd,#8fa3ad)"></div>
  <h3>Equipment Cleaning<br>&amp; Sanitisation</h3>
  <p>Full cleaning, sanitising and tune up kit service for food service equipment.</p>
  <span class="go"><svg width="20" height="20" viewBox="0 0 20 20"><path d="M8 6l4 4-4 4" stroke="#fff" stroke-width="2.4" fill="none"/></svg></span>
</div>
<div class="abs card" style="left:344px">
  <div class="card-img" role="img" aria-label="Photo: pressure cleaning of playground equipment" style="background:linear-gradient(160deg,#6b83b0,#c96a58)"></div>
  <h3>High Pressure &amp;<br>Playground Cleaning</h3>
  <p>High pressure gurney cleaning of hard surfaces and playground equipment.</p>
  <span class="go"><svg width="20" height="20" viewBox="0 0 20 20"><path d="M8 6l4 4-4 4" stroke="#fff" stroke-width="2.4" fill="none"/></svg></span>
</div>
<div class="abs card" style="left:615px">
  <div class="card-img" role="img" aria-label="Photo: commercial property interior being cleaned" style="background:linear-gradient(160deg,#8a6b4f,#b9b5ae)"></div>
  <h3>General Cleaning &amp;<br>Facility Management</h3>
  <p>General cleaning and property facilities management for commercial sites.</p>
  <span class="go"><svg width="20" height="20" viewBox="0 0 20 20"><path d="M8 6l4 4-4 4" stroke="#fff" stroke-width="2.4" fill="none"/></svg></span>
</div>
<div class="abs card" style="left:885px">
  <div class="card-img" role="img" aria-label="Photo: tradespeople and cleaners on a project site" style="background:linear-gradient(160deg,#4b4d50,#8c8e90)"></div>
  <h3>Project &amp; Recruiting<br>Services</h3>
  <p>Cleaners, handymen, mechanics, warehousing staff and electricians: submit your resume.</p>
  <span class="go"><svg width="20" height="20" viewBox="0 0 20 20"><path d="M8 6l4 4-4 4" stroke="#fff" stroke-width="2.4" fill="none"/></svg></span>
</div>

<!-- support -->
<div class="abs support"></div>
<div class="abs photo-circle" role="img" aria-label="Photo: support agent wearing a headset at a desk" style="top:2038px;left:90px;width:438px;height:438px;background:linear-gradient(150deg,#c9c6c0,#7e8b99)"></div>
<h2 class="abs support-title">CUSTOMER SUPPORT &amp; INSURANCE</h2>
<div class="abs rule light" style="top:2116px;left:588px"></div>
<ul class="abs list">
  <li><svg width="14" height="14" viewBox="0 0 14 14"><circle cx="7" cy="7" r="7" fill="#fff"/><path d="M3.8 7.2l2.2 2.1 4.2-4.4" stroke="#1b2f63" stroke-width="1.8" fill="none"/></svg><span>National Customer Support phone for all support enquiries:<br>1300 555 010</span></li>
  <li><svg width="14" height="14" viewBox="0 0 14 14"><circle cx="7" cy="7" r="7" fill="#fff"/><path d="M3.8 7.2l2.2 2.1 4.2-4.4" stroke="#1b2f63" stroke-width="1.8" fill="none"/></svg><span>National Customer Support email: service@brightvale.example</span></li>
  <li><svg width="14" height="14" viewBox="0 0 14 14"><circle cx="7" cy="7" r="7" fill="#fff"/><path d="M3.8 7.2l2.2 2.1 4.2-4.4" stroke="#1b2f63" stroke-width="1.8" fill="none"/></svg><span>Service Call outs we are on site within 24 hours</span></li>
  <li><svg width="14" height="14" viewBox="0 0 14 14"><circle cx="7" cy="7" r="7" fill="#fff"/><path d="M3.8 7.2l2.2 2.1 4.2-4.4" stroke="#1b2f63" stroke-width="1.8" fill="none"/></svg><span>Our Head Office is available: Monday to Friday from 8am to 5pm</span></li>
</ul>
<a class="abs btn" style="top:2395px;left:588px;width:180px">READ MORE</a>
<svg class="band" style="top:2560px" width="1200" height="99" viewBox="0 2560 1200 99" aria-hidden="true"><path d="M0 2658Q600 2462 1200 2658V2659H0Z" fill="#fff"/></svg>

<!-- gallery -->
<div class="abs mark" style="top:2676px;left:583px"></div>
<h2 class="abs center sec-title" style="top:2717px">Photo Gallery</h2>
<div class="abs rule" style="top:2767px;left:546px"></div>
<div class="abs shot" style="top:2824px;left:74px;background:linear-gradient(135deg,#1f4b8c,#a9b4bd)" role="img" aria-label="Photo: twin slush machine bowls"></div>
<div class="abs shot" style="top:2824px;left:435px;background:linear-gradient(135deg,#8d8d8b,#c8c7c2)" role="img" aria-label="Photo: stainless double sink"></div>
<div class="abs shot" style="top:2824px;left:795px;background:linear-gradient(135deg,#3a3a3a,#9a9893)" role="img" aria-label="Photo: drink dispenser valves"></div>
<div class="abs shot" style="top:3062px;left:74px;background:linear-gradient(135deg,#5a4a3c,#b9b3a8)" role="img" aria-label="Photo: fryer units on a tiled floor"></div>
<div class="abs shot" style="top:3062px;left:435px;background:linear-gradient(135deg,#4a4f55,#b8bcc0)" role="img" aria-label="Photo: disassembled machine parts"></div>
<div class="abs shot" style="top:3062px;left:795px;background:linear-gradient(135deg,#c9c3b6,#eeeae2)" role="img" aria-label="Photo: cleaned parts laid out on a bench"></div>

<!-- people -->
<div class="abs people"></div>
<h2 class="abs sec-title light" style="top:3520px;left:74px">Our People</h2>
<div class="abs rule light" style="top:3574px;left:76px"></div>
<h3 class="abs" style="top:3607px;left:76px;color:#fff;font-size:22px;font-weight:700">Brightvale Service Technician attributes</h3>
<p class="abs body-text" style="top:3653px;left:76px;width:560px;color:#fff">Our people are carefully selected and are recruited from qualified trades backgrounds or with equivalent on the job experience. They are career focused cleaning and maintenance professionals.</p>
<a class="abs btn" style="top:3779px;left:76px;width:180px">READ MORE</a>
<div class="abs photo-circle" role="img" aria-label="Photo: smiling technician in cap and apron on the phone" style="top:3455px;left:670px;width:438px;height:438px;background:linear-gradient(150deg,#e3e6ea,#5a77b0)"></div>
<svg class="band" style="top:3987px" width="1200" height="69" viewBox="0 3987 1200 69" aria-hidden="true"><path d="M0 4055Q600 3919 1200 4055V4056H0Z" fill="#fff"/></svg>

<!-- clients -->
<div class="abs mark" style="top:4075px;left:583px"></div>
<h2 class="abs center sec-title" style="top:4130px">Our Clients</h2>
<div class="abs rule" style="top:4182px;left:546px"></div>
<p class="abs center lead" style="top:4212px;line-height:31px;padding:0 80px">Brightvale has established a strong reputation as being reliable, responsive and dedicated to fulfilling<br>our customers and partners cleaning service needs.</p>
<p class="abs center body-text" style="top:4274px;font-size:14px">This reputation is reflected in the organisations that have trusted us to support them both locally and nationally, including:</p>
<div class="abs client" style="left:74px"><i></i>Goldarch</div>
<div class="abs client" style="left:252px"><i></i>Fizzwell</div>
<div class="abs client" style="left:430px"><i></i>Grillhouse</div>
<div class="abs client" style="left:608px;font-size:16px">Kitchenforge</div>
<div class="abs client" style="left:785px"><i></i>Crispco</div>
<div class="abs client" style="left:963px"><i></i>Hartline</div>

<!-- footer -->
<div class="abs footer"></div>
<svg class="band" style="top:4484px" width="1200" height="72" viewBox="0 4484 1200 72" aria-hidden="true"><path d="M0 4484H1200V4485Q600 4625 0 4485Z" fill="#fff"/></svg>
<div class="abs" style="top:4535px;left:550px;width:100px;height:100px;border-radius:50%;background:#fff"></div>
<div class="abs" style="top:4560px;left:575px;width:50px;height:50px;border-radius:50%;background:var(--navy)"></div>

<div class="abs foot-col" style="left:74px">
  <h4>SITE MAP</h4>
  <ul><li>Home</li><li>Services</li><li>About Us</li><li>Our People</li><li>Safety &amp; Compliance</li><li>Contact</li></ul>
</div>
<div class="abs foot-col" style="left:307px">
  <h4>SERVICES</h4>
  <ul><li>Equipment Cleaning &amp; Sanitisation</li><li>High Pressure &amp; Playground Cleaning</li><li>General Cleaning &amp; Facilities</li><li>Project &amp; Recruiting Services</li></ul>
</div>
<div class="abs foot-col" style="left:608px">
  <h4>CONTACT INFO</h4>
  <ul>
    <li style="line-height:26px;padding-top:2px">27 Harbour Lane, Suite 12<br>Newport QLD 4020</li>
    <li class="contact-row"><svg width="13" height="13" viewBox="0 0 24 24"><path fill="#fff" d="M6.6 10.8a15.1 15.1 0 0 0 6.6 6.6l2.2-2.2a1 1 0 0 1 1-.25 11.4 11.4 0 0 0 3.6.57 1 1 0 0 1 1 1V20a1 1 0 0 1-1 1A17 17 0 0 1 3 4a1 1 0 0 1 1-1h3.5a1 1 0 0 1 1 1c0 1.25.2 2.45.57 3.57a1 1 0 0 1-.25 1z"/></svg>(07) 5550 0123</li>
    <li class="contact-row"><svg width="13" height="11" viewBox="0 0 13 11"><rect width="13" height="11" rx="1" fill="#fff"/><path d="M0.5 1l6 5 6-5" stroke="#1b2f63" stroke-width="1.3" fill="none"/></svg>info@brightvale.example</li>
  </ul>
</div>
<div class="abs foot-col" style="left:883px">
  <h4>EMAIL SIGN UP</h4>
  <div class="email-input">Enter Email Address</div>
  <div class="signup">SIGN UP</div>
</div>

<div class="abs bottombar"></div>
<p class="abs copy">Copyright © 2020. Company Name. All Right Reserved</p>
<div class="abs social" aria-label="Social links"><span></span><span></span><span></span><span></span><span></span></div>

</body>
</html>
```